Mental Health Clinic Website

website for a mental health clinic. two files describing the website are attached, in case of conflicting info the word document is priority.

Target Market(s)

Ohio / Pennsylvania residents

Industry/Entity Type

Health Care

Coding

Coded - Design and coding required

Number of Pages Required

5+ page

Requirements
Must have
• see attached

```html
<!DOCTYPE html>
<html lang="en">
<head>
<meta charset="utf-8">
<title>Brightwater Wellness Center</title>
<link href="https://fonts.googleapis.com/css2?family=Lato:wght@400;700;900&display=swap" rel="stylesheet">
<style>
:root{
  --blue:#1d5aa8;
  --blue-dark:#123f7e;
  --navy:#0e3470;
  --green:#5aa847;
  --red:#e3161c;
  --ink:#222;
  --text:#3a3a3a;
  --light:#eef3fa;
  --white:#fff;
}
*{box-sizing:border-box;margin:0;padding:0}
html,body{width:1200px;height:4478px;overflow:hidden}
body{font-family:'Lato',sans-serif;color:var(--text);background:var(--white);position:relative}
section,header,footer{position:absolute;left:0;width:1200px}
.abs{position:absolute}

/* hero */
.hero{top:0;height:690px;background:linear-gradient(180deg,#7fb6e6 0%,#cfe3f0 45%,#7ea83c 62%,#4f8a22 100%)}
.brand{left:100px;top:0;width:240px;height:255px;background:var(--white);text-align:center;padding-top:176px}
.brand-name{font-weight:900;font-size:19px;line-height:23px;color:var(--ink)}
.brand-mark{position:absolute;left:96px;top:34px;width:48px;height:48px;border-radius:50%;background:var(--green)}
.nav{left:100px;top:255px;width:240px;height:250px}
.nav ul{position:absolute;left:0;top:30px;width:240px;list-style:none;text-align:center}
.nav li{font-size:18px;color:var(--white);height:37px;line-height:37px;position:relative}
.nav li::after{content:"";position:absolute;left:80px;right:80px;bottom:0;height:1px;background:rgba(255,255,255,.5)}
.nav li:last-child::after{display:none}
.dots{left:560px;top:634px;display:flex;gap:10px}
.dots span{width:16px;height:16px;border-radius:50%;border:2px solid var(--white)}
.dots span.on{background:var(--white)}

/* welcome */
.welcome{top:690px;height:683px}
.section-title{font-weight:700;font-size:38px;color:var(--ink);text-align:center;line-height:46px}
.welcome .section-title{position:absolute;top:60px;width:100%}
.tree{left:120px;top:175px;width:270px;height:405px;border-radius:135px 135px 30px 30px;background:radial-gradient(circle at 50% 35%,#f2a23b,#d8433a 40%,#4aa0d8 65%,#5aa847 90%)}
.welcome-text{left:418px;top:194px;width:660px;font-size:17px;line-height:25px}
.welcome-text p{margin-bottom:25px}

/* about */
.about{top:1373px;height:940px;background:linear-gradient(125deg,#1d58ad 0%,#1f6aa6 45%,#3e9a62 80%,#5cab45 100%);color:var(--white)}
.about h2{left:130px;top:98px;font-size:38px;font-weight:700}
.about-intro{left:136px;top:160px;width:470px;font-size:17px;line-height:26px;font-weight:700}
.langs{left:136px;top:352px;font-size:16px;font-weight:700;line-height:23px}
.langs .grid{display:grid;grid-template-columns:105px 105px;margin-top:16px}
.about-photo{left:640px;top:60px;width:420px;height:420px;border-radius:50%;border:6px solid var(--white);background:radial-gradient(circle at 50% 40%,#f4f1ec,#d9cfc4 60%,#b9a79a)}
.team{left:103px;top:545px;width:1000px;display:flex;justify-content:space-between}
.member{width:190px;text-align:center}
.member .photo{width:140px;height:140px;margin:0 auto;border-radius:50%;border:4px solid var(--white);background:linear-gradient(160deg,#e8e2dc,#a9b9c8)}
.member .name{font-weight:700;font-size:18px;margin-top:24px}
.member .role{font-size:14px;margin-top:2px}
.member .bio{font-size:12px;line-height:15px;margin:10px auto 0;width:150px;opacity:.9}
.member .btn{display:block;width:160px;height:32px;margin:22px auto 0;border:1.5px solid var(--white);font-size:12px;font-weight:700;line-height:29px}

/* services */
.services{top:2313px;height:932px}
.services .section-title{position:absolute;top:72px;width:100%}
.tiles{left:112px;top:153px;display:flex;gap:14px}
.tile{width:184px;height:191px;border:1.5px solid #c9c9c9;text-align:center;color:var(--blue);font-weight:700;font-size:14px;line-height:17px;padding:22px 8px 0;display:flex;flex-direction:column;align-items:center;position:relative}
.tile svg{width:70px;height:70px;margin-bottom:12px;flex:none}
.tile.active{background:var(--red);border-color:var(--red);color:var(--white)}
.tile.active::after{content:"";position:absolute;left:50%;bottom:-30px;margin-left:-30px;border-left:30px solid transparent;border-right:30px solid transparent;border-top:30px solid var(--red)}
.tile .label{flex:1;display:flex;align-items:center}
.detail-panel{left:561px;top:427px;width:529px;height:400px;background:var(--blue);color:var(--white);padding:52px 40px 0 99px}
.detail-panel h3{font-size:26px;font-weight:700;margin-bottom:22px}
.detail-panel p{font-size:16px;line-height:22px;margin-bottom:22px;color:#dbe7f7}
.detail-photo{left:113px;top:469px;width:520px;height:308px;background:linear-gradient(120deg,#f4f6f9,#cdd6e0 55%,#9fb0c4)}

/* reads */
.reads{top:3245px;height:486px;background:var(--light)}
.reads .section-title{position:absolute;top:55px;width:100%}
.book{top:137px;width:476px;height:230px;background:var(--white);border:1px solid #dfe4ea;padding:45px 20px 0 244px}
.book .cover{position:absolute;left:25px;top:45px;width:200px;height:175px}
.book h4{color:var(--blue);font-size:21px;font-weight:700}
.book .author{color:var(--green);font-weight:700;font-size:14px;margin:6px 0 8px}
.book p{font-size:12px;line-height:16px;width:200px}

/* contact */
.contact{top:3731px;height:591px;background:linear-gradient(135deg,#eceeee,#e1e4e4)}
.contact-card{left:134px;top:164px;width:403px;height:323px;background:var(--white);box-shadow:0 2px 10px rgba(0,0,0,.12);padding:60px 0 0 52px}
.contact-card h3{color:var(--blue);font-size:30px;font-weight:700;margin-bottom:24px}
.contact-card p{color:var(--blue-dark);font-weight:700;font-size:16px;line-height:26px}
.appt{left:740px;top:84px;width:350px;height:418px;background:var(--green);padding:24px 31px 0;color:var(--white)}
.appt h3{font-size:27px;font-weight:700;text-align:center;margin-bottom:22px}
.field{height:36px;background:var(--white);margin-bottom:16px;color:#777;font-size:13px;line-height:36px;padding-left:10px}
.check{display:flex;gap:10px;font-size:13px;font-weight:700;line-height:16px;margin-top:-2px}
.check span.box{width:16px;height:16px;background:var(--white);flex:none}
.submit{margin-top:16px;height:50px;background:#1b3a26;text-align:center;font-weight:700;font-size:18px;line-height:50px}

/* footer */
.footer-bar{top:4322px;height:90px;background:var(--navy);color:var(--white);display:flex;align-items:center;justify-content:center;gap:75px;font-size:17px;font-weight:700}
.footer-bar .item{display:flex;align-items:center;gap:12px}
.footer-bar svg{width:22px;height:22px}
.copy{left:0;width:1200px;top:4412px;height:66px;background:var(--blue-dark);color:#c7d6ee;font-size:13px;text-align:center;line-height:66px}
</style>
</head>
<body>

<header class="hero" role="img" aria-label="Photo of a person in a green meadow with arms raised under a blue sky">
  <div class="abs brand">
    <span class="brand-mark"></span>
    <div class="brand-name">Brightwater<br>Wellness Center</div>
  </div>
  <nav class="abs nav">
    <svg class="abs" style="left:0;top:0" width="240" height="250" viewBox="0 0 240 250"><path d="M0 0H240V220C170 200 90 240 0 250Z" fill="#1d5aa8"/></svg>
    <ul>
      <li>Home</li><li>About Us</li><li>Services</li><li>Good Reads</li><li>Contact</li>
    </ul>
  </nav>
  <div class="abs dots"><span></span><span class="on"></span><span></span></div>
</header>

<section class="welcome">
  <h1 class="section-title">Welcome to<br>Brightwater Wellness Center</h1>
  <div class="abs tree" role="img" aria-label="Illustration of a colourful tree held by a hand"></div>
  <div class="abs welcome-text">
    <p>Each individual is unique with unique personality and unique needs. Therefore we provide individual treatment customized for you or your child. Multiculturalism also informs our practice. We are a full service mental health practice with the capacity to serve adults, children, teens and their parents.</p>
    <p>We provide high quality evidence based treatment and care including medication management, pharmacogenomic testing, individual psychotherapy, group psychotherapy, art therapy, CBT, DBT and trauma therapy. Our providers are experts in treating variety of illnesses such as depression, anxiety, schizophrenia, ADHD, gender identity concerns and PTSD.</p>
    <p>We are experienced in a variety of methods that help people achieve their psychological goals, and we will discuss with you the best ways to attain the health and wellness that you deserve. We are committed to helping you achieve your optimal level of emotional functioning and fulfill a successful life.</p>
  </div>
</section>

<section class="about">
  <h2 class="abs">About Us</h2>
  <p class="abs about-intro">You will find a number of highly specialized – experienced and caring therapists and psychiatrists in Brightwater Center. We provide medication management and psychotherapy (counseling) across the lifespan.<br>– children, teens and adults.</p>
  <div class="abs langs">Other than English, we speak the following languages
    <div class="grid"><span>Spanish</span><span>Farsi</span><span>German</span><span>Hebrew</span></div>
  </div>
  <div class="abs about-photo" role="img" aria-label="Photo of a woman meditating in a lotus pose"></div>
  <div class="abs team">
    <div class="member"><div class="photo" role="img" aria-label="Staff portrait"></div><div class="name">Person Name</div><div class="role">Designation</div><div class="bio">Aenean ac turpis egestas Cras id elit integer quis urna Ut ante enim dapibus malesuada fring</div><span class="btn">Make an appointment</span></div>
    <div class="member"><div class="photo" role="img" aria-label="Staff portrait"></div><div class="name">Person Name</div><div class="role">Designation</div><div class="bio">Aenean ac turpis egestas Cras id elit integer quis urna Ut ante enim dapibus malesuada fring</div><span class="btn">Make an appointment</span></div>
    <div class="member"><div class="photo" role="img" aria-label="Staff portrait"></div><div class="name">Person Name</div><div class="role">Designation</div><div class="bio">Aenean ac turpis egestas Cras id elit integer quis urna Ut ante enim dapibus malesuada fring</div><span class="btn">Make an appointment</span></div>
    <div class="member"><div class="photo" role="img" aria-label="Staff portrait"></div><div class="name">Person Name</div><div class="role">Designation</div><div class="bio">Aenean ac turpis egestas Cras id elit integer quis urna Ut ante enim dapibus malesuada fring</div><span class="btn">Make an appointment</span></div>
    <div class="member"><div class="photo" role="img" aria-label="Staff portrait"></div><div class="name">Person Name</div><div class="role">Designation</div><div class="bio">Aenean ac turpis egestas Cras id elit integer quis urna Ut ante enim dapibus malesuada fring</div><span class="btn">Make an appointment</span></div>
  </div>
</section>

<section class="services">
  <h2 class="section-title">Our Services</h2>
  <div class="abs tiles">
    <div class="tile active">
      <svg viewBox="0 0 70 70" fill="none" stroke="currentColor" stroke-width="2.5"><rect x="16" y="12" width="38" height="50" rx="3"/><rect x="27" y="7" width="16" height="9" rx="2"/><path d="M35 26v14M28 33h14M24 50h22"/></svg>
      <span class="label">MEDICATION MANAGEMENT</span>
    </div>
    <div class="tile">
      <svg viewBox="0 0 70 70" fill="none" stroke="currentColor" stroke-width="2.5"><circle cx="35" cy="17" r="8"/><path d="M22 45c0-9 6-16 13-16s13 7 13 16"/><circle cx="14" cy="40" r="5"/><circle cx="56" cy="40" r="5"/><path d="M6 62c0-6 4-10 8-10s8 4 8 10M48 62c0-6 4-10 8-10s8 4 8 10"/></svg>
      <span class="label">PSYCHOTHERAPY: INDIVIDUAL, GROUP, COUPLES, AND FAMILY</span>
    </div>
    <div class="tile">
      <svg viewBox="0 0 70 70" fill="none" stroke="currentColor" stroke-width="2.5"><path d="M35 10C20 10 8 21 8 35s11 25 24 25c4 0 5-3 3-6s0-7 4-7h8c8 0 15-6 15-14C62 20 50 10 35 10Z"/><circle cx="22" cy="30" r="4"/><circle cx="34" cy="22" r="4"/><circle cx="47" cy="27" r="4"/></svg>
      <span class="label">ART THERAPY</span>
    </div>
    <div class="tile">
      <svg viewBox="0 0 70 70" fill="none" stroke="currentColor" stroke-width="2.5"><path d="M20 60V46c-6-4-9-10-9-17 0-12 10-21 23-21s24 9 24 21c0 12-10 21-22 21H30v10"/><circle cx="34" cy="29" r="7"/><path d="M34 18v4M34 36v4M23 29h4M41 29h4"/></svg>
      <span class="label">TREATMENT APPROACH</span>
    </div>
    <div class="tile">
      <svg viewBox="0 0 70 70" fill="none" stroke="currentColor" stroke-width="2.5"><circle cx="35" cy="20" r="10"/><path d="M14 62c0-13 9-22 21-22s21 9 21 22Z"/><path d="M35 46v10M30 51h10"/></svg>
      <span class="label">TREATMENT AREAS</span>
    </div>
  </div>
  <div class="abs detail-panel">
    <h3>MEDICATION MANAGEMENT</h3>
    <p>Pellentesque faucibus Ut accumsan ultricies elit Maecenas at justo id velit placerat molestie Donec dictum lectus non odio Cras a ante vitae enim</p>
    <p>Mauris nunc quam venenatis nec euismod sit amet egestas placerat est Pellentesque habitant morbi tristique senectus et netus et malesuada fames ac turpis egestas Cras id elit integer quis urna Ut ante enim dapibus malesuada fringilla eu condi</p>
  </div>
  <div class="abs detail-photo" role="img" aria-label="Photo of a doctor writing a prescription beside pill bottles"></div>
</section>

<section class="reads">
  <h2 class="section-title">Good Reads</h2>
  <article class="abs book" style="left:110px">
    <div class="cover" role="img" aria-label="Photo of old books on a shelf" style="background:linear-gradient(90deg,#5a2a1c,#a4562e 30%,#2f4a6a 55%,#8a2b24 80%,#c9a26a)"></div>
    <h4>Book Title here</h4>
    <div class="author">Author Name</div>
    <p>Pellentesque faucibus Ut accumsan ultricies elit Maecenas at justo id velit placerat molestie Donec dictum lectus non odio Cras a ante vitae enim</p>
  </article>
  <article class="abs book" style="left:609px">
    <div class="cover" role="img" aria-label="Photo of an open book" style="background:linear-gradient(180deg,#4a4744,#8a8580 45%,#e9e4da 70%,#bdb5a8)"></div>
    <h4>Book Title here</h4>
    <div class="author">Author Name</div>
    <p>Pellentesque faucibus Ut accumsan ultricies elit Maecenas at justo id velit placerat molestie Donec dictum lectus non odio Cras a ante vitae enim</p>
  </article>
</section>

<section class="contact" role="img" aria-label="Street map of the clinic area">
  <div class="abs contact-card">
    <h3>Contact Us</h3>
    <p>4280 Meadowbrook Road, Suite 210,<br>Fairmont, OH 44502<br>(330) 555-0172<br>hello@brightwaterwc.com</p>
  </div>
  <form class="abs appt">
    <h3>Appointment Request</h3>
    <div class="field">First Name</div>
    <div class="field">Last Name</div>
    <div class="field">Email</div>
    <div class="field">Phone</div>
    <div class="check"><span class="box"></span><span>Please contact me for an appointment</span></div>
    <div class="submit">SUBMIT</div>
  </form>
</section>

<footer class="footer-bar">
  <span class="item"><svg viewBox="0 0 24 24" fill="#fff"><path d="M12 2a7 7 0 0 0-7 7c0 5 7 13 7 13s7-8 7-13a7 7 0 0 0-7-7Zm0 10a3 3 0 1 1 0-6 3 3 0 0 1 0 6Z"/></svg>4280 Meadowbrook Road, Suite 210, Fairmont, OH 44502</span>
  <span class="item"><svg viewBox="0 0 24 24" fill="#fff"><path d="M6.6 10.8a15 15 0 0 0 6.6 6.6l2.2-2.2c.3-.3.7-.4 1-.2 1.1.4 2.3.6 3.6.6.6 0 1 .4 1 1V20c0 .6-.4 1-1 1A17 17 0 0 1 3 4c0-.6.4-1 1-1h3.5c.6 0 1 .4 1 1 0 1.3.2 2.5.6 3.6.1.3 0 .7-.2 1Z"/></svg>(330) 555-0172</span>
  <span class="item"><svg viewBox="0 0 24 24" fill="#fff"><path d="M3 5h18v14H3Zm2 2v.4l7 4.6 7-4.6V7Z"/></svg>hello@brightwaterwc.com</span>
</footer>
<div class="abs copy">© 2019 Company Name All right reserved</div>

</body>
</html>
```